Heritage Hollow Business Cards

Require a business card design. <br/><br/>Needs to include logo (either round or long version) plus these details:<br/>Maya Torvell<br/>Heritage Hollow<br/>maya@kelvadtrading.com.au<br/>02 6481 7395<br/>PO Box Glenwarra NSW 2791<br/>www.heritagehollow.com.au<br/><br/>I need in an editable format so that I can create for multiple staff members. <br/><br/>

Target Market(s)

We are an online store selling renovation products to home owners are builders. Looking for a classic classy design.

Industry/Entity Type

Home And Garden

Contact Information for Business Card

Maya Torvell
Heritage Hollow
maya@kelvadtrading.com.au
02 6481 7395
PO Box Glenwarra NSW 2791
www.heritagehollow.com.au

Colors

Designer to choose colors to be used in the design.

Requirements
Must have
• Must include Logo.

```html
<!DOCTYPE html>
<html lang="en">
<head>
<meta charset="utf-8">
<title>Heritage Hollow Business Cards</title>
<link rel="stylesheet" href="https://fonts.googleapis.com/css2?family=Lato:wght@400;900&display=swap">
<style>
  :root {
    --page: #e4e4e4;
    --card-dark: #000000;
    --card-light: #ffffff;
    --ink: #111111;
    --ink-soft: #666666;
    --ink-mid: #333333;
    --rule: #1a1a1a;
  }
  * { margin: 0; padding: 0; box-sizing: border-box; }
  html, body {
    width: 1200px;
    height: 900px;
    overflow: hidden;
    background: var(--page);
    font-family: "Lato", sans-serif;
  }
  .sheet {
    position: relative;
    width: 1200px;
    height: 900px;
  }
  .card {
    position: absolute;
    left: 270px;
    width: 660px;
    height: 390px;
    border-radius: 22px;
    overflow: hidden;
    box-shadow: 0 6px 18px rgba(0,0,0,0.18);
  }
  .card--front { top: 40px; background: var(--card-dark); }
  .card--back { top: 470px; background: var(--card-light); }

  .front-brand {
    position: absolute;
    left: 0; top: 0; width: 100%; height: 100%;
    display: flex;
    align-items: center;
    justify-content: center;
    gap: 18px;
  }
  .front-brand__circle {
    width: 58px; height: 58px;
    border: 1.5px solid var(--card-light);
    border-radius: 50%;
  }
  .front-brand__name {
    color: var(--card-light);
    font-weight: 400;
    font-size: 40px;
    letter-spacing: 0.5px;
  }

  .back-brand {
    position: absolute;
    left: 60px; top: 92px;
    width: 206px; height: 206px;
    border: 1.5px solid var(--ink-mid);
    border-radius: 50%;
    display: flex;
    align-items: center;
    justify-content: center;
    text-align: center;
  }
  .back-brand__name {
    color: var(--ink);
    font-weight: 400;
    font-size: 30px;
    line-height: 1.05;
  }
  .divider {
    position: absolute;
    left: 338px; top: 84px;
    width: 1.5px; height: 222px;
    background: var(--rule);
  }
  .details {
    position: absolute;
    left: 372px; top: 78px;
    color: var(--ink-soft);
    font-size: 15px;
    line-height: 1.3;
  }
  .details__name {
    color: var(--ink);
    font-weight: 900;
    font-size: 26px;
    line-height: 1.1;
    margin-bottom: 4px;
  }
  .details__company { margin-bottom: 12px; }
  .details__address { margin-bottom: 12px; }
  .contact { list-style: none; }
  .contact__item {
    display: flex;
    align-items: center;
    gap: 10px;
    margin-bottom: 3px;
  }
  .contact__icon { width: 14px; height: 14px; flex: none; }
</style>
</head>
<body>
<main class="sheet">
  <section class="card card--front" aria-label="Card front">
    <div class="front-brand">
      <span class="front-brand__circle"></span>
      <span class="front-brand__name">Heritage Hollow</span>
    </div>
  </section>

  <section class="card card--back" aria-label="Card back">
    <div class="back-brand">
      <span class="back-brand__name">Heritage<br>Hollow</span>
    </div>
    <div class="divider"></div>
    <div class="details">
      <p class="details__name">Maya Torvell</p>
      <p class="details__company">Heritage Hollow</p>
      <p class="details__address">PO Box Glenwarra<br>NSW 2791</p>
      <ul class="contact">
        <li class="contact__item">
          <svg class="contact__icon" viewBox="0 0 16 16" aria-hidden="true">
            <path d="M3.5 1.5l2.5 0.5 1 3-1.6 1.2a8 8 0 0 0 4.4 4.4L11 9l3 1 0.5 2.5-2 2A11 11 0 0 1 1.5 3.5z" fill="#111"/>
          </svg>
          <span>02 6481 7395</span>
        </li>
        <li class="contact__item">
          <svg class="contact__icon" viewBox="0 0 16 16" aria-hidden="true">
            <rect x="1" y="3" width="14" height="10" fill="#111"/>
            <path d="M1 3l7 6 7-6" fill="none" stroke="#fff" stroke-width="1.2"/>
          </svg>
          <span>maya@kelvadtrading.com.au</span>
        </li>
        <li class="contact__item">
          <svg class="contact__icon" viewBox="0 0 16 16" aria-hidden="true">
            <circle cx="8" cy="8" r="7" fill="#111"/>
            <g fill="none" stroke="#fff" stroke-width="0.9">
              <ellipse cx="8" cy="8" rx="3" ry="7"/>
              <path d="M1 8h14M2.5 4.5h11M2.5 11.5h11"/>
            </g>
          </svg>
          <span>www.heritagehollow.com.au</span>
        </li>
      </ul>
    </div>
  </section>
</main>
</body>
</html>
```